Wordpress coded website (5 page-home page, contact form & 3 common pages) for Skiing event

I would like a WordPress site designed for our Ski & Snowboard event. The site is to have 5 total pages.

Hosting has been setup (Bright Hostings) and WordPress installed.

Requirements:
Front page with Landscape slide, Snowbook feed, 4 menu items, footer and small description section.

3 Separate pages to be created, with a similar layout with landscape image slider and large text section (content provided)

1 Contact us page with the below form sections
- Name
- School
- Position
- Email
- Phone
- Message

Target Market(s)

School teachers and school students

Industry/Entity Type

Tourism

Number of Pages Required

5+ page

Colors

Designer to choose colors to be used in the design.

Requirements
Must have
• Must include event logo attached in brief. Must include Snowbook feed on homepage

```html
<!DOCTYPE html>
<html lang="en">
<head>
<meta charset="utf-8">
<title>Mount Alder SKI Challenge</title>
<link href="https://fonts.googleapis.com/css2?family=Lato:wght@400;700;900&display=swap" rel="stylesheet">
<style>
:root{
  --blue:#0e96e4;
  --blue-dark:#2d4f9c;
  --ink:#222;
  --text:#333;
  --dark:#1f1f1f;
  --darker:#161616;
  --line:#d5d5d5;
  --white:#fff;
}
*{box-sizing:border-box;margin:0;padding:0}
html,body{width:1017px;height:1200px;overflow:hidden;background:var(--white)}
body{font-family:'Lato',sans-serif;color:var(--text);position:relative}
.abs{position:absolute}

/* top contact strip */
.topbar-mail{left:522px;top:0;width:270px;height:30px;background:#2a2a2a;clip-path:polygon(0 0,100% 0,100% 100%,10px 100%);color:var(--white);font-size:13.5px;display:flex;align-items:center;padding-left:14px;gap:8px}
.topbar-phone{left:790px;top:0;width:145px;height:30px;background:var(--blue);clip-path:polygon(0 0,100% 0,calc(100% - 10px) 100%,0 100%);color:var(--white);font-size:14px;display:flex;align-items:center;padding-left:12px;gap:8px}
.ico-circ{width:19px;height:19px;border-radius:50%;background:var(--white);display:flex;align-items:center;justify-content:center}
.top-rule{left:0;top:0;width:1017px;height:2px;background:#2a2a2a}

/* header */
.brand{left:83px;top:0;width:150px;height:176px;background:var(--white);clip-path:polygon(0 0,100% 0,100% 85%,50% 100%,0 85%);box-shadow:0 2px 6px rgba(0,0,0,.2);z-index:3;display:flex;flex-direction:column;align-items:center;justify-content:center;gap:8px;padding-bottom:18px}
.brand-dot{width:34px;height:34px;border-radius:50%;background:var(--blue)}
.brand-name{font-weight:900;color:var(--blue);font-size:17px;text-align:center;line-height:1.15}
.nav{left:400px;top:64px;display:flex;align-items:flex-start}
.nav a{font-size:15px;color:var(--ink);text-decoration:none;padding:0 26px;border-left:1px solid #ccc;line-height:16px;position:relative}
.nav a:first-child{border-left:none;color:var(--blue);font-weight:700}
.nav-mark{position:absolute;left:50%;top:22px;width:15px;height:15px;margin-left:-7px;border-radius:50%;background:var(--blue)}

/* hero */
.hero{left:0;top:113px;width:1017px;height:462px;background:linear-gradient(180deg,#3a3e47 0%,#8aa2bd 30%,#c9d9ea 55%,#dfe6ee 70%,#a9b8c8 100%)}
.hero-caption{left:0;top:512px;width:1017px;text-align:center;color:var(--white);font-size:34px;font-weight:700;text-shadow:0 1px 3px rgba(0,0,0,.4)}
.arrow{top:330px;width:36px;height:36px;background:rgba(60,60,60,.75);display:flex;align-items:center;justify-content:center}

/* about */
.about-title{left:84px;top:612px;font-size:28px;font-weight:700;color:var(--blue)}
.about-mark{left:84px;top:661px;width:18px;height:20px;border-radius:50%;background:#c8c8c8}
.about-rule{left:115px;top:671px;width:558px;height:2px;border-top:1px solid var(--line);border-bottom:1px solid #eee}
.about-body{left:85px;top:700px;width:592px;font-size:13px;line-height:23.6px;color:var(--text)}
.about-body strong{color:var(--ink)}
.about-body p+p{margin-top:4px}

/* feed */
.feed{left:711px;top:619px;width:222px;height:249px;border:2px solid var(--blue-dark)}
.feed-head{height:31px;background:var(--blue-dark);color:var(--white);display:flex;justify-content:space-between;align-items:center;padding:0 12px;font-size:11px}
.feed-head b{font-weight:900;font-size:11.5px}
.feed-item{display:flex;gap:8px;margin:0 10px;padding:10px 0 8px;border-bottom:1px dotted #ccc;height:66px}
.feed-item:nth-child(4){border-bottom:none}
.thumb{width:43px;height:35px;flex:none}
.feed-item a{display:block;font-size:10px;line-height:14.5px;color:var(--blue-dark);text-decoration:none}
.feed-item small{display:block;font-size:8px;color:#333;margin-top:3px}
.feed-foot{position:absolute;left:0;bottom:0;width:100%;border-top:1px solid #ddd;font-size:10px;color:#555;padding:7px 10px}

/* footer */
.footer{left:0;top:912px;width:1017px;height:252px;background:var(--dark)}
.f-col{color:var(--white)}
.f-title{font-size:17px;color:var(--white);font-weight:400}
.f-title span{color:var(--blue)}
.f-rule{height:1px;background:#444;margin-top:10px;position:relative}
.f-rule::before{content:"";position:absolute;left:0;top:0;width:24px;height:1px;background:#999}
.f-sep{top:955px;width:1px;height:176px;background:#333}
.links{list-style:none;margin-top:6px}
.links li{font-size:13.5px;line-height:30px;padding-left:2px;color:var(--white)}
.links li::before{content:"•";font-size:9px;margin-right:6px;vertical-align:2px}
.contact-name{font-size:14px;font-weight:700;margin-top:10px;color:var(--white)}
.contact-addr{font-size:11.5px;line-height:17.5px;color:var(--white)}
.contact-row{display:flex;align-items:center;gap:10px;font-size:12px;margin-top:14px;color:var(--white)}
.field{width:218px;border:1px solid #444;background:#1a1a1a;color:#ddd;font-size:11px;padding:0 10px;display:flex;align-items:center;height:29px;margin-top:6px}
.field.msg{height:36px;align-items:flex-start;padding-top:8px}
.submit{width:88px;height:29px;background:var(--blue);color:var(--white);font-size:14px;font-weight:700;display:flex;align-items:center;justify-content:center;margin-top:7px;letter-spacing:.3px}
.f-brand{left:792px;top:950px;width:146px;height:190px;display:flex;flex-direction:column;align-items:center;justify-content:center;gap:10px}
.f-brand-dot{width:46px;height:46px;border-radius:50%;background:#8a8a8a}
.f-brand-name{font-size:19px;font-weight:900;color:#9a9a9a;text-align:center;line-height:1.15}
.bottombar{left:0;top:1163px;width:1017px;height:37px;background:var(--darker);color:var(--white);font-size:11.5px;display:flex;align-items:center;padding-left:85px}
.socials{right:83px;top:1171px;display:flex;gap:7px}
.socials i{width:20px;height:20px;border-radius:50%;background:var(--white);display:block}
</style>
</head>
<body>

<header>
  <div class="abs top-rule"></div>
  <div class="abs topbar-mail">
    <span class="ico-circ"><svg width="10" height="8" viewBox="0 0 10 8"><rect x="0.5" y="0.5" width="9" height="7" fill="#2a2a2a"/><path d="M0.5 0.8 5 4.5 9.5 0.8" stroke="#fff" fill="none" stroke-width="1"/></svg></span>
    enquiry@alderskichallenge.com.au
  </div>
  <div class="abs topbar-phone">
    <span class="ico-circ"><svg width="10" height="8" viewBox="0 0 10 8"><rect x="0.5" y="0.5" width="9" height="7" fill="#0e96e4"/><path d="M0.5 0.8 5 4.5 9.5 0.8" stroke="#fff" fill="none" stroke-width="1"/></svg></span>
    02 5550 1840
  </div>

  <div class="abs brand">
    <span class="brand-dot"></span>
    <span class="brand-name">Mount Alder<br>Ski Challenge</span>
  </div>

  <nav class="abs nav">
    <a href="#">Home<span class="nav-mark"></span></a>
    <a href="#">Event</a>
    <a href="#">Mt Alder</a>
    <a href="#">Itinerary</a>
    <a href="#">Contact Us</a>
  </nav>
</header>

<section>
  <div class="abs hero" role="img" aria-label="Slider photo: row of colourful skis and ski boots resting on snow"></div>
  <div class="abs arrow" style="left:26px"><svg width="10" height="14" viewBox="0 0 10 14"><path d="M7 2 2 7l5 5" stroke="#fff" stroke-width="2" fill="none"/></svg></div>
  <div class="abs arrow" style="left:955px"><svg width="10" height="14" viewBox="0 0 10 14"><path d="M3 2l5 5-5 5" stroke="#fff" stroke-width="2" fill="none"/></svg></div>
  <h1 class="abs hero-caption">Welcome To About Mount Alder SKI Challenge</h1>
</section>

<main>
  <h2 class="abs about-title">About Mount Alder SKI Challenge</h2>
  <span class="abs about-mark"></span>
  <div class="abs about-rule"></div>
  <div class="abs about-body">
    <p><strong>Wednesday 11th July &amp; Thursday 12th July 2018.</strong><br>
    The Mt Alder Ski Challenge is the first event of its kind in the Southern Hemisphere offering high school students from Australia to face off against New Zealand locals on the ski fields of Mt Alder. With no race experience necessary, the event provides a great fun experience for those enjoying their first time on the slopes as well as providing a chance for experienced skiers and snowboarders to test themselves against the clock and other competitors.</p>
    <p><strong>Notes:</strong> No experience necessary badge to appear on page</p>
  </div>

  <aside class="abs feed">
    <div class="feed-head"><span>Recent Activity</span><b>Snowbook</b></div>
    <div class="feed-item">
      <div class="thumb" role="img" aria-label="Thumbnail: lodge among trees" style="background:#3f6d5a"></div>
      <div><a href="#">Lorem ipsum dolor sit amet the consectetuer adipi.</a><small>2 people recommended this.</small></div>
    </div>
    <div class="feed-item">
      <div class="thumb" role="img" aria-label="Thumbnail: skis on snow" style="background:#a9a39a"></div>
      <div><a href="#">Lorem ipsum dolor sit amet the adipiscing elit, sed di nonummy</a><small>3 people recommended this.</small></div>
    </div>
    <div class="feed-item">
      <div class="thumb" role="img" aria-label="Thumbnail: ski boots close up" style="background:#3e5f84"></div>
      <div><a href="#">Lorem ipsum dolor sit amet the consectetuer adipiscing.</a><small>2 people recommended this.</small></div>
    </div>
    <div class="feed-foot">Snowbook Social Plugin</div>
  </aside>
</main>

<footer>
  <div class="abs footer"></div>

  <div class="abs f-col" style="left:83px;top:943px;width:110px">
    <h3 class="f-title">QUICK <span>LINKS</span></h3>
    <div class="f-rule"></div>
    <ul class="links">
      <li>Home</li><li>Event</li><li>Mt Alder</li><li>Itinerary</li><li>Contact Us</li>
    </ul>
  </div>
  <div class="abs f-sep" style="left:221px"></div>

  <div class="abs f-col" style="left:252px;top:943px;width:206px">
    <h3 class="f-title">CONTACT <span>DETAILS</span></h3>
    <div class="f-rule"></div>
    <div class="contact-name">Mount Alder SKI Challenge</div>
    <div class="contact-addr">48 Snowline Rd. Glenvale,<br>Riverton - 12345</div>
    <div class="contact-row"><svg width="11" height="11" viewBox="0 0 11 11"><path d="M2 0.5 4 2.8 3 4.3c.7 1.5 2 2.8 3.6 3.6L8.1 6.9 10.5 9 9 10.5C4.5 10.2.8 6.5.5 2z" fill="#fff"/></svg>02 5550 1840</div>
    <div class="contact-row"><svg width="11" height="11" viewBox="0 0 11 11"><rect x="3" y="0.5" width="5" height="3" fill="#fff"/><rect x="0.5" y="4" width="10" height="4.5" fill="#fff"/><rect x="3" y="7" width="5" height="3.5" fill="#fff" stroke="#1f1f1f"/></svg>02 5550 1840</div>
    <div class="contact-row"><svg width="11" height="9" viewBox="0 0 11 9"><rect x="0.5" y="0.5" width="10" height="8" fill="#fff"/><path d="M0.5 0.8 5.5 5 10.5 0.8" stroke="#1f1f1f" fill="none"/></svg>enquiry@alderskichallenge.com.au</div>
  </div>
  <div class="abs f-sep" style="left:485px"></div>

  <div class="abs f-col" style="left:516px;top:943px;width:220px">
    <h3 class="f-title">QUICK <span>INQUIRY</span></h3>
    <div class="f-rule"></div>
    <div class="field" style="margin-top:11px">Name</div>
    <div class="field">Email</div>
    <div class="field msg">Message</div>
    <div class="submit">SUBMIT</div>
  </div>
  <div class="abs f-sep" style="left:765px"></div>

  <div class="abs f-brand">
    <span class="f-brand-dot"></span>
    <span class="f-brand-name">Mount Alder<br>Ski Challenge</span>
  </div>

  <div class="abs bottombar">Copyright © 2017 Mount Alder SKI Challenge. All Right Reserved.</div>
  <div class="abs socials"><i></i><i></i><i></i><i></i></div>
</footer>

</body>
</html>
```